Road Construction Company needs business cards

We would like a new business card designed for our business.

We're a road construction company based in Qld, Australia.

Can the business card please have the following information on it.

Name: Warren Halbeck
Position: General Manager
Phone: 0472 915 348
Email: Warren.halbeck@tovrin.com.au
Address: 87 Marrow Ave, Pendlebay, QLD, 4023
Website: www.tovrin.com.au

Visually we'd like the card to be professional and simple.

Attached is our logo.

Our website is www.tovrin.com.au

Target Market(s)

Men aged 25-60

Contact Information for Business Card

As listed in project description

Font styles to use
Serif

Requirements
Must have
• Large logo on back of card

```html
<!DOCTYPE html>
<html lang="en">
<head>
<meta charset="utf-8">
<title>Tovrin Business Card</title>
<link rel="stylesheet" href="https://fonts.googleapis.com/css2?family=Krona+One&family=Exo+2:wght@400;500&display=swap">
<style>
  :root {
    --brand-blue: #0054a6;
    --panel-light: #f3f1f1;
    --text-white: #ffffff;
    --page-bg: #e4e6ea;
  }
  * { margin: 0; padding: 0; box-sizing: border-box; }
  html, body {
    width: 1200px;
    height: 900px;
    overflow: hidden;
    background: var(--page-bg);
  }
  .business-card {
    position: absolute;
    left: 150px;
    top: 172px;
    width: 900px;
    height: 556px;
    display: flex;
    box-shadow: 0 10px 30px rgba(0, 0, 0, 0.15);
  }
  .brand-side {
    width: 420px;
    height: 100%;
    background: var(--panel-light);
    display: flex;
    align-items: center;
    justify-content: center;
  }
  .brand-name {
    font-family: "Krona One", sans-serif;
    font-size: 54px;
    color: var(--brand-blue);
    letter-spacing: 1px;
  }
  .contact-side {
    width: 480px;
    height: 100%;
    background: var(--brand-blue);
    color: var(--text-white);
    padding: 148px 0 0 49px;
    font-family: "Exo 2", sans-serif;
  }
  .person-name {
    font-family: "Krona One", sans-serif;
    font-size: 25px;
    line-height: 1;
    letter-spacing: 0.5px;
  }
  .person-role {
    font-size: 24px;
    line-height: 1.2;
    margin-top: 3px;
  }
  .contact-list {
    list-style: none;
    margin-top: 24px;
  }
  .contact-item {
    display: flex;
    align-items: center;
    font-size: 24px;
    line-height: 33px;
  }
  .contact-icon {
    width: 24px;
    height: 24px;
    margin-right: 11px;
    flex-shrink: 0;
  }
  .address {
    font-style: normal;
    font-size: 24px;
    line-height: 33px;
    margin-top: 18px;
  }
</style>
</head>
<body>
  <div class="business-card">
    <div class="brand-side">
      <span class="brand-name">TOVRIN</span>
    </div>
    <div class="contact-side">
      <h1 class="person-name">WARREN HALBECK</h1>
      <p class="person-role">General Manager</p>
      <ul class="contact-list">
        <li class="contact-item">
          <svg class="contact-icon" viewBox="0 0 24 24" aria-hidden="true">
            <path d="M6.6 3.5l3 3.2-1.8 2.2c1.2 2.6 3.2 4.6 5.8 5.8l2.2-1.8 3.2 3-2 2.6c-0.5 0.6-1.3 0.8-2 0.6C9.6 17.5 5.5 13.4 3.9 7.9c-0.2-0.7 0-1.5 0.6-2z" fill="none" stroke="#fff" stroke-width="1.8" stroke-linejoin="round"/>
            <path d="M14 3.5a7 7 0 0 1 6.5 6.5M14 7a3.5 3.5 0 0 1 3 3" fill="none" stroke="#fff" stroke-width="1.6" stroke-linecap="round"/>
          </svg>
          <span>0472 915 348</span>
        </li>
        <li class="contact-item">
          <svg class="contact-icon" viewBox="0 0 24 24" aria-hidden="true">
            <rect x="1.5" y="5" width="21" height="14" fill="#fff"/>
            <path d="M1.5 5l10.5 8 10.5-8M1.5 19l8-7M22.5 19l-8-7" fill="none" stroke="#0054a6" stroke-width="1.4"/>
          </svg>
          <span>Warren.halbeck@tovrin.com.au</span>
        </li>
        <li class="contact-item">
          <svg class="contact-icon" viewBox="0 0 24 24" aria-hidden="true">
            <g fill="none" stroke="#fff" stroke-width="1.6">
              <circle cx="12" cy="12" r="10"/>
              <ellipse cx="12" cy="12" rx="4.5" ry="10"/>
              <path d="M2 12h20M3.5 7h17M3.5 17h17"/>
            </g>
          </svg>
          <span>www.tovrin.com.au</span>
        </li>
      </ul>
      <address class="address">
        87 Marrow Ave<br>
        Pendlebay, QLD, 4023
      </address>
    </div>
  </div>
</body>
</html>
```